Cedar Brook Stables, LLC

Equestrian business card to promote equine retirement, farm sitting, short term board. Located in Aiken, SC.
Updates
Updated color schemes.
Contact Information for Business Card
Contact info, description of work.
Colors
0094D4
00A9DD
6FCCEA
C7EBF8
E9F6FB
59FF00
82FF00
B8FF75
E3FFCB
F4FFEA
F0912C
F2A743
F7CA91
FBE8D2
FDF5EE

```html
<!DOCTYPE html>
<html lang="en">
<head>
<meta charset="utf-8">
<title>Cedar Brook Stables – Business Card</title>
<link rel="stylesheet" href="https://fonts.googleapis.com/css2?family=Bebas+Neue&family=Poppins:wght@400;500;600&display=swap">
<style>
  :root {
    --backdrop: #1c1c1c;
    --card: #121212;
    --band-green: #0b7410;
    --tagline-yellow: #ffe500;
    --name-gold: #ffbf00;
    --icon-gold: #f5b100;
    --text-light: #c9c9c9;
    --brand-silver: #d4d4d4;
    --divider: #8a8a8a;
    --mark-fill: #f2a743;
  }
  * { box-sizing: border-box; margin: 0; padding: 0; }
  html, body { width: 1200px; height: 900px; overflow: hidden; }
  body {
    background: var(--backdrop);
    font-family: "Poppins", sans-serif;
    display: flex;
    flex-direction: column;
    align-items: center;
    justify-content: center;
    gap: 44px;
  }
  .card {
    position: relative;
    width: 660px;
    height: 377px;
    background: var(--card);
    box-shadow: 0 10px 28px rgba(0,0,0,.55);
    overflow: hidden;
  }
  .card__band {
    position: absolute;
    left: 0; right: 0; bottom: 0;
    height: 14px;
    background: var(--band-green);
  }

  /* Front */
  .brand {
    position: absolute;
    top: 34px;
    left: 0; right: 0;
    display: flex;
    flex-direction: column;
    align-items: center;
    gap: 14px;
  }
  .brand__mark {
    width: 150px; height: 150px;
    border-radius: 50%;
    background: var(--mark-fill);
  }
  .brand__name {
    font-weight: 600;
    font-size: 26px;
    letter-spacing: 1px;
    color: var(--brand-silver);
    text-transform: uppercase;
  }
  .tagline {
    position: absolute;
    left: 0; right: 0;
    bottom: 46px;
    text-align: center;
    font-weight: 500;
    font-size: 19px;
    letter-spacing: .4px;
    color: var(--tagline-yellow);
    text-transform: uppercase;
  }

  /* Back */
  .person {
    position: absolute;
    left: 48px;
    top: 112px;
  }
  .person__name {
    font-family: "Bebas Neue", sans-serif;
    font-weight: 400;
    font-size: 56px;
    line-height: 1;
    color: var(--name-gold);
    letter-spacing: .5px;
  }
  .person__role {
    font-size: 19px;
    color: var(--text-light);
    margin-top: 2px;
  }
  .divider {
    position: absolute;
    left: 292px;
    top: 112px;
    width: 1px;
    height: 96px;
    background: var(--divider);
  }
  .contact {
    position: absolute;
    left: 316px;
    top: 114px;
    list-style: none;
    display: flex;
    flex-direction: column;
    gap: 6px;
  }
  .contact__item {
    display: flex;
    align-items: center;
    gap: 10px;
    font-size: 18px;
    color: var(--text-light);
    white-space: nowrap;
  }
  .contact__icon { width: 20px; height: 20px; flex: none; }
  .address {
    position: absolute;
    left: 48px;
    bottom: 50px;
    font-size: 19px;
    color: var(--text-light);
  }
</style>
</head>
<body>

  <section class="card card--front" aria-label="Business card front">
    <div class="brand">
      <span class="brand__mark"></span>
      <span class="brand__name">Cedar Brook Stables, LLC</span>
    </div>
    <p class="tagline">Short Term Board | Farm Sitting | Equine Retirement</p>
    <div class="card__band"></div>
  </section>

  <section class="card card--back" aria-label="Business card back">
    <div class="person">
      <h1 class="person__name">Marcus Hale</h1>
      <p class="person__role">Managing Director</p>
    </div>
    <div class="divider"></div>
    <ul class="contact">
      <li class="contact__item">
        <svg class="contact__icon" viewBox="0 0 24 24" aria-hidden="true">
          <path fill="var(--icon-gold)" d="M6.6 10.8a15.1 15.1 0 0 0 6.6 6.6l2.2-2.2c.3-.3.7-.4 1-.2 1.1.4 2.3.6 3.6.6.6 0 1 .4 1 1V20c0 .6-.4 1-1 1A17 17 0 0 1 3 4c0-.6.4-1 1-1h3.5c.6 0 1 .4 1 1 0 1.3.2 2.5.6 3.6.1.3 0 .7-.2 1z"/>
        </svg>
        <span>803-555-0147</span>
      </li>
      <li class="contact__item">
        <svg class="contact__icon" viewBox="0 0 24 24" aria-hidden="true">
          <rect x="2" y="5" width="20" height="14" rx="1" fill="var(--icon-gold)"/>
          <path d="M2.5 6 12 13l9.5-7" fill="none" stroke="var(--card)" stroke-width="1.6"/>
        </svg>
        <span>info@cedarbrookstables.com</span>
      </li>
      <li class="contact__item">
        <svg class="contact__icon" viewBox="0 0 24 24" aria-hidden="true">
          <g fill="none" stroke="var(--icon-gold)" stroke-width="2">
            <circle cx="12" cy="12" r="9"/>
            <ellipse cx="12" cy="12" rx="4" ry="9"/>
            <path d="M3 12h18M5 7h14M5 17h14"/>
          </g>
        </svg>
        <span>cedarbrookstables.com</span>
      </li>
    </ul>
    <p class="address">1450 Meadow Lane, Aiken, SC 29801</p>
    <div class="card__band"></div>
  </section>

</body>
</html>
```